Book Cover for a book on Quiet Ventures

I am self-publishing my book on Brindlecart and need a book cover made. Below are the details. See attached templates for size we need to use. I also attached a previous cover we had made that I liked. The problem with it was they were two boys helping each other but the book is about women. I'm open to your ideas on the cover though, but I wanted to show you a style I liked as an idea.
Front of Cover
Book Title: Quiet Ventures
Book Subtitle: Unvarnished Notes of a Woman Founder
Author Name: Lorna T. Pelham
Add on the Spine of Cover: Quiet Ventures and Lorna T. Pelham
Back of the Cover Text:
Quiet Ventures: Unvarnished Notes of a Woman Founder is an honest account of a business owner’s experience attempting to navigate the start-up community while also pursuing spiritual growth. Author Lorna Pelham defines a spiritual entrepreneur as “someone who runs an enterprise with the purpose of growing love rather than material gain.” This book discusses the three dimensions of Quiet Ventures:
1. The business is an integral part of the founder’s spiritual journey.
2. Employees working for the spiritual enterprise, whether they know it or not, encounter this company because it's part of their spiritual path.
3. The business itself has a life force of its own and its purpose is to further the kingdom of heaven on earth.
These three dimensions happen simultaneously and work together to produce the greatest possible result. However, this can feel confusing to a founder juggling these dimensions while also trying to manage and run a business. This is not a formulaic self-help book or roadmap. Rather, it is a compilation of personal reflections that often seem at odds with the traditional world of entrepreneurship.
Below the description add my picture (see attached for my picture)
Bio text:
Lorna Pelham founded Halvex with the vision of ushering in a life-long education system that shifts away from standardization to one that empowers people to live their purpose. In college, Lorna interned for Open Meadow, a women’s empowerment initiative where she recognized her passion for helping people find their voice. Lorna's 20-year journey has come full circle to empowering other female CEOs who are pursuing the path of Quiet Ventures.
NOTE: Please note that Brindlecart puts a bar code on the bottom right of the back cover as is noted on the attached template.
Size template is attached to the brief, here are the sizes typed out:
# Description Width (in) Height (in)
1 Full Cover 12.79 9.25
2 Front Cover 6 9
3 Safe Area 5.875 8.75
4 Bleed 0.125 0.125
5 Margin 0.125 0.125
6 Spine 0.54 9
7 Spine Safe Area 0.415 8.75
8 Spine Margin 0.062 0.062
9 Barcode Margin 0.25 0.25
Pre-publication checklist
BRINDLECART TIPS for the final cover:
1. Save as a PDF. Your cover must be a single PDF that includes the back cover, spine, and front cover as one image.
2. Flatten all transparencies. These can cause the file to print with missing or distorted content. Consult your software's documentation to learn how.
3. Embed your fonts. Consult your software's documentation to learn how.
4. Remove crop marks, color bars, template text. Crop marks are lines showing where pages should be trimmed. Color bars are strips with a series of patches used to ensure color balance during printing. Also, remove any template text, PDF creation guides, or software references.
5. Ensure your cover image meets the minimum resolution of 300 DPI (dots per inch).
6. Optimize PDFs. Optimization is useful to reduce your file size, allowing for higher performance when transferring, uploading, viewing, and printing the files.
7. Remove file security. Locked or encrypted files will fail review.
Target Market(s)
Women who want to be CEOs or are currently CEOs of companies.
Industry/Entity Type
Entrepreneurship, business, spirituality
Requirements
Must have
- Just the text on the description. A very welcoming feel.
Nice to have
- I like the idea of having a sunrise/sunset in the image somehow like in the example I attached to the brief, but again I'm open.
Should not have
- Please don't put any yoga or meditation poses or hands outstretched. I have a lot of interesting ones that look like my example so if you are going to submit after Saturday 10/29, please only do so if you have a new idea! Thanks!

```html
<!DOCTYPE html>
<html lang="en">
<head>
<meta charset="utf-8">
<title>Quiet Ventures – Book Cover</title>
<link href="https://fonts.googleapis.com/css2?family=Noto+Serif:ital,wght@0,400;1,400&display=swap" rel="stylesheet">
<style>
  :root {
    --ink: #111110;
    --ink-glow: #2a2c20;
    --gold: #f5d30f;
    --paper: #ffffff;
    --text: #f2f2f0;
    --rule: #8a8a84;
    --frame: #4a4a3a;
  }
  * { margin: 0; padding: 0; box-sizing: border-box; }
  html, body { width: 1200px; height: 874px; overflow: hidden; background: var(--ink); }
  .cover {
    position: relative;
    width: 1200px; height: 874px;
    background: radial-gradient(ellipse 320px 300px at 300px 300px, var(--ink-glow), var(--ink) 75%);
    font-family: "Noto Serif", Georgia, serif;
    font-weight: 400;
    color: var(--text);
    overflow: hidden;
  }

  /* Back cover */
  .back-blurb {
    position: absolute; left: 38px; top: 60px; width: 501px;
    font-size: 12.6px; line-height: 16.9px; letter-spacing: 0.07em;
    text-align: justify;
  }
  .back-blurb p { margin-bottom: 16.9px; }
  .back-blurb .lead { color: var(--gold); }
  .back-blurb ol { list-style: none; margin: 0 0 16.9px 46px; }
  .back-blurb li { margin-bottom: 16.9px; }
  .back-blurb li:last-child { margin-bottom: 0; }

  .author-photo {
    position: absolute; left: 38px; top: 486px; width: 124px; height: 123px;
    border: 3px solid var(--frame);
    background: linear-gradient(180deg, #f6f4f2 0%, #efe7e4 55%, #e2527a 85%, #d9456f 100%);
  }
  .author-bio {
    position: absolute; left: 184px; top: 480px; width: 363px;
    font-size: 12.6px; line-height: 16.9px; letter-spacing: 0.07em;
    text-align: justify;
  }

  /* Spine */
  .spine-title, .spine-subtitle, .spine-author {
    position: absolute; writing-mode: vertical-rl; white-space: nowrap; line-height: 1.3;
  }
  .spine-title {
    left: 596px; top: 105px; color: var(--gold);
    font-size: 24px; letter-spacing: 0.06em;
  }
  .spine-subtitle {
    left: 576px; top: 167px; font-style: italic;
    font-size: 16.5px; letter-spacing: 0.05em;
  }
  .spine-author {
    left: 588px; top: 622px;
    font-size: 20px; letter-spacing: 0.1em;
  }

  /* Front cover */
  .front { position: absolute; left: 637px; top: 0; width: 563px; height: 874px; }
  .front-art { position: absolute; left: 0; top: 0; width: 563px; height: 600px; }
  .front-title {
    position: absolute; left: 0; width: 563px; top: 586px;
    text-align: center; color: var(--gold);
    font-size: 46px; font-weight: 400; line-height: 53px; letter-spacing: 0.08em;
  }
  .front-rule {
    position: absolute; left: 51px; top: 698px; width: 452px; height: 1px;
    background: linear-gradient(90deg, transparent, var(--rule) 15%, var(--rule) 85%, transparent);
  }
  .front-subtitle {
    position: absolute; left: 0; width: 563px; top: 709px;
    text-align: center; font-style: italic; white-space: nowrap;
    font-size: 23px; letter-spacing: 0.03em;
  }
  .front-author {
    position: absolute; left: 0; width: 563px; top: 788px;
    text-align: center; color: var(--paper);
    font-size: 27px; letter-spacing: 0.12em;
  }
</style>
</head>
<body>
<main class="cover">

  <section class="back">
    <div class="back-blurb">
      <p><span class="lead">QUIET VENTURES:</span> Unvarnished Notes of a Woman Founder is an honest account of a business owner’s experience attempting to navigate the start-up community while also pursuing spiritual growth. Author Lorna Pelham defines a spiritual entrepreneur as “someone who runs an enterprise with the purpose of growing love rather than material gain.” This book discusses the three dimensions of Quiet Ventures:</p>
      <ol>
        <li>1. The business is an integral part of the founder’s spiritual journey.</li>
        <li>2. Employees working for the spiritual enterprise, whether they know it or not, encounter this company because it's part of their spiritual path.</li>
        <li>3. The business itself has a life force of its own and its purpose is to further the kingdom of heaven on earth.</li>
      </ol>
      <p>These three dimensions happen simultaneously and work together to produce the greatest possible result. However, this can feel confusing to a founder juggling these dimensions while also trying to manage and run a business. This is not a formulaic self-help book or roadmap. Rather, it is a compilation of personal reflections that often seem at odds with the traditional world of entrepreneurship.</p>
    </div>

    <div class="author-photo" role="img" aria-label="Portrait photo of the author"></div>

    <p class="author-bio">Lorna Pelham founded Halvex with the vision of ushering in a life-long education system that shifts away from standardization to one that empowers people to live their purpose. In college, Lorna interned for Open Meadow, a women’s empowerment initiative where she recognized her passion for helping people find their voice. Lorna's 20-year journey has come full circle to empowering other female CEOs who are pursuing the path of Quiet Ventures.</p>
  </section>

  <section class="spine">
    <span class="spine-title">QUIET VENTURES</span>
    <span class="spine-subtitle">Unvarnished Notes of a Woman Founder</span>
    <span class="spine-author">Lorna T. Pelham</span>
  </section>

  <section class="front">
    <svg class="front-art" viewBox="0 0 563 600" width="563" height="600">
      <defs>
        <linearGradient id="sky" x1="0" y1="0" x2="0" y2="1">
          <stop offset="0" stop-color="#f6c66a"/>
          <stop offset="0.45" stop-color="#e9a748"/>
          <stop offset="1" stop-color="#6a5a2a"/>
        </linearGradient>
        <radialGradient id="sun" cx="0.3" cy="0.18" r="0.55">
          <stop offset="0" stop-color="#fffbe8"/>
          <stop offset="0.35" stop-color="#fbe0a0" stop-opacity="0.8"/>
          <stop offset="1" stop-color="#f2b050" stop-opacity="0"/>
        </radialGradient>
        <linearGradient id="shade" x1="0" y1="0" x2="1" y2="0">
          <stop offset="0" stop-color="#2b2a16" stop-opacity="0"/>
          <stop offset="0.55" stop-color="#24301c" stop-opacity="0.55"/>
          <stop offset="0.75" stop-color="#1f2a18" stop-opacity="0.75"/>
          <stop offset="1" stop-color="#2b2a16" stop-opacity="0.1"/>
        </linearGradient>
        <linearGradient id="band" x1="0" y1="0" x2="1" y2="0">
          <stop offset="0" stop-color="#5a5a55"/>
          <stop offset="0.2" stop-color="#ffffff"/>
          <stop offset="0.8" stop-color="#ffffff"/>
          <stop offset="1" stop-color="#e0e0dc"/>
        </linearGradient>
        <linearGradient id="dark-band" x1="0" y1="0" x2="1" y2="0">
          <stop offset="0" stop-color="#8a8a84"/>
          <stop offset="0.5" stop-color="#2a2a26"/>
          <stop offset="1" stop-color="#2a2a26"/>
        </linearGradient>
      </defs>
      <g role="img" aria-label="Photo of a woman working on a laptop by a tall window at sunrise">
        <polygon points="0,0 563,0 563,450 276,545 0,449" fill="url(#sky)"/>
        <polygon points="0,0 563,0 563,450 276,545 0,449" fill="url(#sun)"/>
        <polygon points="0,0 563,0 563,450 276,545 0,449" fill="url(#shade)"/>
      </g>
      <polygon points="0,449 276,545 0,487" fill="url(#dark-band)"/>
      <polygon points="0,487 276,545 563,450 563,489 276,574 0,520" fill="url(#band)"/>
    </svg>

    <h1 class="front-title">QUIET<br>VENTURES</h1>
    <div class="front-rule"></div>
    <p class="front-subtitle">Unvarnished Notes of a Woman Founder</p>
    <p class="front-author">Lorna T. Pelham</p>
  </section>

</main>
</body>
</html>
```